Bramblewood Card Company Business Cards

We are a trading card store with Glimmorax, sports and other TCG cards, we need a business card design that encompasses a clean cut, modern style with a retro flare. website is bramblewoodcardco.com for reference. Can utilize a comic book era feel or a more modern outdoor feel to utilize the "Pacific Northwest" elements of tress, mountains, etc.

Industry/Entity Type

Trading cards and collectibles

Contact Information for Business Card

business name, email address, phone number, name, owner job title

Font styles to use
Sans Serif

```html
<!DOCTYPE html>
<html lang="en">
<head>
<meta charset="utf-8">
<title>Bramblewood Card Company – Business Cards</title>
<link href="https://fonts.googleapis.com/css2?family=Montserrat:wght@400;500;700;800&display=swap" rel="stylesheet">
<style>
  :root {
    --backdrop: #1c1c1c;
    --card-grey: #7d7d7d;
    --card-grey-light: #8a8a8a;
    --accent-blue: #2ec4e6;
    --ink-white: #ffffff;
  }
  * { margin: 0; padding: 0; box-sizing: border-box; }
  html, body { width: 1200px; height: 900px; overflow: hidden; }
  body {
    background: var(--backdrop);
    font-family: "Montserrat", sans-serif;
    display: flex; flex-direction: column; align-items: center; justify-content: center;
    gap: 40px;
  }
  .card {
    position: relative;
    width: 620px; height: 354px;
    background: linear-gradient(135deg, var(--card-grey) 0%, var(--card-grey-light) 100%);
    overflow: hidden;
  }
  .brand-mark {
    display: flex; align-items: center; gap: 12px;
    color: var(--ink-white);
    font-weight: 800;
    text-transform: uppercase;
    letter-spacing: 0.06em;
    line-height: 1.15;
  }
  .brand-mark__dot {
    flex: none; border-radius: 50%; background: var(--accent-blue);
  }
  .card--front { display: flex; align-items: center; justify-content: center; }
  .card--front .brand-mark { font-size: 26px; }
  .card--front .brand-mark__dot { width: 46px; height: 46px; }

  .card--back .brand-mark {
    position: absolute; top: 42px; right: 40px; font-size: 17px;
  }
  .card--back .brand-mark__dot { width: 32px; height: 32px; }

  .identity { position: absolute; top: 64px; left: 0; }
  .identity__tab {
    position: absolute; left: 0; top: 2px; width: 12px; height: 38px;
    background: var(--accent-blue); border-radius: 0 4px 4px 0;
  }
  .identity__name {
    margin-left: 40px; color: var(--accent-blue);
    font-size: 30px; font-weight: 800; letter-spacing: 0.06em; line-height: 1;
  }
  .identity__role {
    margin-left: 32px; margin-top: 6px; color: var(--ink-white);
    font-size: 14px; font-weight: 500; letter-spacing: 0.04em;
  }
  .divider {
    position: absolute; top: 160px; left: 30px; right: 36px; height: 2px;
    background: var(--accent-blue);
  }
  .contact-list {
    position: absolute; top: 182px; left: 30px; list-style: none;
    color: var(--ink-white); font-size: 14px; font-weight: 500; letter-spacing: 0.03em;
  }
  .contact-list li { display: flex; align-items: center; gap: 10px; height: 24px; }
  .contact-list svg { width: 14px; height: 14px; fill: none; stroke: var(--accent-blue); stroke-width: 2; }
  .contact-list svg .solid { fill: var(--accent-blue); stroke: none; }
  .address {
    position: absolute; right: 36px; bottom: 34px; text-align: right;
    color: var(--ink-white); font-size: 15px; font-weight: 500; letter-spacing: 0.04em; line-height: 1.35;
  }
</style>
</head>
<body>
  <section class="card card--front">
    <div class="brand-mark">
      <span class="brand-mark__dot"></span>
      <span>Bramblewood<br>Card Company</span>
    </div>
  </section>

  <section class="card card--back">
    <div class="brand-mark">
      <span class="brand-mark__dot"></span>
      <span>Bramblewood<br>Card Company</span>
    </div>

    <div class="identity">
      <span class="identity__tab"></span>
      <p class="identity__name">DALEN BROOKS</p>
      <p class="identity__role">MANAGER</p>
    </div>

    <div class="divider"></div>

    <ul class="contact-list">
      <li>
        <svg viewBox="0 0 24 24"><path class="solid" d="M6.6 10.8a15.1 15.1 0 0 0 6.6 6.6l2.2-2.2a1 1 0 0 1 1-.25 11.4 11.4 0 0 0 3.6.57 1 1 0 0 1 1 1V20a1 1 0 0 1-1 1A17 17 0 0 1 3 4a1 1 0 0 1 1-1h3.5a1 1 0 0 1 1 1c0 1.25.2 2.45.57 3.57a1 1 0 0 1-.25 1z"/></svg>
        (206)555-0142
      </li>
      <li>
        <svg viewBox="0 0 24 24"><rect x="6" y="2" width="12" height="20" rx="2"/><line x1="11" y1="18" x2="13" y2="18"/></svg>
        (206)555-01873
      </li>
      <li>
        <svg viewBox="0 0 24 24"><rect class="solid" x="2" y="5" width="20" height="14" rx="1"/><path d="M2 6l10 7 10-7" stroke="#7d7d7d"/></svg>
        info@bramblewoodcardco.com
      </li>
      <li>
        <svg viewBox="0 0 24 24"><circle cx="12" cy="12" r="9"/><line x1="3" y1="12" x2="21" y2="12"/><ellipse cx="12" cy="12" rx="4" ry="9"/></svg>
        www.bramblewoodcardco.com
      </li>
    </ul>

    <p class="address">418 Cedar Ridge Lane<br>Tacoma, WA 98402</p>
  </section>
</body>
</html>
```